Animal Eye Clinic needs a Business card

We are a new veterinary ophthalmology practice (Ridgeline Pet Vision Care) and we need a business card designed. We only see animal eyes - we are not a regular veterinary clinic. We already have a logo. We are looking for a professional, good looking business card to hand out to our clients. We are looking for something simple but professional and contemporary. Our logo is likely the only picture/graphic that needs to be on the card.
Updates

Contact Information for Business Card

Delia Vossman, BSc, DVM, MSc, DipACVO
Veterinary Ophthalmologist

Phone: 250.418.3927
Email: ridgelinepetvisioncare@mailbox-example.net
Website: ridgelinepetvisioncare-example.net
Address: 1874 Thornbury Rd
Kelowna, BC, V1X 4M9

Colors

Designer to choose colors to be used in the design.

Requirements
Must have
• Our logo (attached)

```html
<!DOCTYPE html>
<html lang="en">
<head>
<meta charset="utf-8">
<title>Ridgeline Pet Vision Care – Business Card</title>
<link href="https://fonts.googleapis.com/css2?family=Lato:wght@400;700;900&display=swap" rel="stylesheet">
<style>
  :root {
    --stage: #2b2b2b;
    --card: #1c1c1c;
    --teal: #1b9aaa;
    --grey: #8a8a8a;
    --grey-soft: #6f6f6f;
    --rule: #5a5a5a;
  }
  * { box-sizing: border-box; margin: 0; padding: 0; }
  html, body { width: 1200px; height: 895px; overflow: hidden; }
  body {
    background: var(--stage);
    font-family: "Lato", Arial, sans-serif;
    display: flex;
    flex-direction: column;
    align-items: center;
    justify-content: center;
    gap: 40px;
  }
  .card {
    width: 660px;
    height: 377px;
    background: var(--card);
    position: relative;
    box-shadow: 0 10px 30px rgba(0,0,0,.45);
  }
  .brand {
    display: flex;
    align-items: center;
    gap: 14px;
  }
  .brand-dot {
    width: 34px; height: 34px;
    border-radius: 50%;
    background: var(--teal);
    flex: none;
  }
  .brand-name {
    color: var(--teal);
    font-weight: 900;
    text-transform: uppercase;
    letter-spacing: .5px;
    line-height: 1;
  }

  /* front */
  .card-front .brand {
    position: absolute;
    left: 0; right: 0; top: 150px;
    justify-content: center;
  }
  .card-front .brand-name { font-size: 30px; }
  .card-front .website {
    position: absolute;
    left: 0; right: 0; bottom: 48px;
    text-align: center;
    font-size: 13px;
    color: var(--grey);
    letter-spacing: .3px;
  }
  .website .domain { color: var(--teal); }

  /* back */
  .card-back .brand {
    position: absolute;
    left: 40px; top: 232px;
  }
  .card-back .brand-dot { width: 26px; height: 26px; }
  .card-back .brand-name { font-size: 17px; }
  .divider {
    position: absolute;
    left: 352px; top: 60px;
    width: 1px; height: 250px;
    background: var(--rule);
  }
  .contact {
    position: absolute;
    left: 378px; top: 66px; right: 20px;
    color: var(--grey);
    font-size: 12.5px;
    line-height: 1.4;
  }
  .person-name {
    color: var(--teal);
    font-weight: 900;
    font-size: 24px;
    text-transform: uppercase;
    line-height: 1.05;
  }
  .address { margin-top: 18px; }
  .links { margin-top: 18px; list-style: none; }
  .links li { display: flex; align-items: center; gap: 8px; white-space: nowrap; }
  .links svg { width: 12px; height: 12px; flex: none; fill: var(--teal); }
</style>
</head>
<body>

<section class="card card-front">
  <div class="brand">
    <span class="brand-dot"></span>
    <span class="brand-name">Ridgeline Pet Vision Care</span>
  </div>
  <p class="website">www.<span class="domain">ridgelinepetvisioncare-example</span>.net</p>
</section>

<section class="card card-back">
  <div class="brand">
    <span class="brand-dot"></span>
    <span class="brand-name">Ridgeline Pet Vision Care</span>
  </div>
  <div class="divider"></div>
  <div class="contact">
    <h1 class="person-name">Delia Vossman</h1>
    <p class="credentials">BSc, DVM, MSc, DipACVO</p>
    <p class="role">Veterinary Ophthalmologist</p>
    <p class="address">1874 Thornbury Rd<br>Kelowna, BC, V1X 4M9</p>
    <ul class="links">
      <li>
        <svg viewBox="0 0 24 24"><path d="M6.6 10.8a15 15 0 0 0 6.6 6.6l2.2-2.2a1 1 0 0 1 1-.25 11.4 11.4 0 0 0 3.6.57 1 1 0 0 1 1 1V20a1 1 0 0 1-1 1A17 17 0 0 1 3 4a1 1 0 0 1 1-1h3.5a1 1 0 0 1 1 1c0 1.25.2 2.45.57 3.57a1 1 0 0 1-.25 1z"/></svg>
        <span>250.418.3927</span>
      </li>
      <li>
        <svg viewBox="0 0 24 24"><path d="M2 5h20v14H2z M2 5l10 8 10-8" fill="none" stroke="#1b9aaa" stroke-width="2.4"/></svg>
        <span>ridgelinepetvisioncare@mailbox-example.net</span>
      </li>
      <li>
        <svg viewBox="0 0 24 24"><circle cx="12" cy="12" r="9.5" fill="none" stroke="#1b9aaa" stroke-width="2"/><path d="M2.5 12h19M12 2.5c3 3 3 16 0 19M12 2.5c-3 3-3 16 0 19" fill="none" stroke="#1b9aaa" stroke-width="1.6"/></svg>
        <span class="website">www.<span class="domain">ridgelinepetvisioncare-example</span>.net</span>
      </li>
    </ul>
  </div>
</section>

</body>
</html>
```